Brookvale Estates LLC stationary for a real estate property management company.

Create stationary (letterhead, envelopes, business cards) using Brookvale Estates LLC logo as primary creative element. Stationary design needs to be horizontal, leaving as much space as possible for correspondence copy. See attached Creative Brief and past stationary files for details.

Target Market(s)

Prospective apartment residents and current residents, vendors, and government agencies.

Industry/Entity Type

Property Management

Contact Information for Business Card

Business card employee title: Property Manager. Should include address, phone, fax, email, website, slogan, and Brookvale Estates logo.

Font styles to use
Sans Serif

Colors
0592cd
000000

Requirements
Must have
• Tone should be conservative, institutional, business (i.e. banking, finance, real estate). Must include: address, phone, fax, website, and slogan (see attached Creative Brief). Should be a horizontal design, leaving as much room as possible for letter correspondence copy.
Nice to have
• Please use an Arial or Helvetica style font.
Should not have
• Letterhead layout should leave as much room as possible for copy.

```html
<!DOCTYPE html>
<html lang="en">
<head>
<meta charset="utf-8">
<title>Brookvale Estates LLC – Business Cards</title>
<link href="https://fonts.googleapis.com/css2?family=Arimo:ital,wght@0,400;0,700;1,700&display=swap" rel="stylesheet">
<style>
  :root {
    --brand-blue: #0592cd;
    --brand-deep: #0f6aa8;
    --ink: #444444;
    --paper: #f3f3f3;
    --stage: #2b2b2b;
    --back-light: #6b6b6b;
    --back-dark: #464646;
    --white: #ffffff;
  }
  * { margin: 0; padding: 0; box-sizing: border-box; }
  html, body { width: 1200px; height: 793px; overflow: hidden; }
  body {
    position: relative;
    background: var(--stage);
    font-family: "Arimo", Arial, sans-serif;
  }
  .card {
    position: absolute;
    width: 496px;
    height: 283px;
    overflow: hidden;
  }
  .card-front { left: 91px; top: 88px; background: var(--paper); }
  .card-back {
    background: linear-gradient(135deg, var(--back-light) 0%, var(--back-dark) 55%, var(--back-dark) 100%);
  }
  .back-01 { left: 622px; top: 87px; }
  .back-02 { left: 90px; top: 425px; }
  .back-03 { left: 622px; top: 426px; }

  .card-label {
    position: absolute;
    width: 496px;
    text-align: center;
    color: var(--white);
    font-size: 11px;
    font-weight: 700;
    font-style: italic;
  }
  .label-front { left: 91px; top: 388px; width: 460px; }
  .label-back-01 { left: 622px; top: 388px; width: 630px; left: 558px; }
  .label-back-02 { left: 90px; top: 728px; width: 460px; }
  .label-back-03 { left: 622px; top: 728px; width: 460px; left: 662px; }

  /* front */
  .front-accent {
    position: absolute;
    left: -150px; top: -40px;
    width: 340px; height: 340px;
    border-radius: 50%;
    background: linear-gradient(160deg, var(--brand-blue), var(--brand-deep));
  }
  .front-info {
    position: absolute;
    right: 22px; top: 30px;
    text-align: right;
    color: var(--ink);
  }
  .company-name {
    color: var(--brand-blue);
    font-weight: 700;
    line-height: 1;
  }
  .front-info .company-name .line-1 { display: block; font-size: 36px; letter-spacing: -0.5px; }
  .front-info .company-name .line-2 { display: block; font-size: 17px; letter-spacing: 3px; margin-top: 4px; }
  .person-name {
    margin-top: 18px;
    color: var(--brand-deep);
    font-size: 18px;
    font-weight: 700;
  }
  .person-title { font-size: 13px; margin-top: 2px; }
  .address { margin-top: 14px; font-size: 12px; line-height: 16px; }
  .contact { margin-top: 10px; font-size: 12px; line-height: 16px; }

  /* backs */
  .slogan { color: var(--white); font-weight: 700; font-size: 12.5px; }
  .back-01 .slogan { position: absolute; left: 0; right: 0; top: 256px; text-align: center; padding-left: 80px; }
  .back-02 .company-name {
    position: absolute; left: 0; right: 0; top: 128px;
    text-align: center; color: var(--white);
  }
  .back-02 .line-1 { display: block; font-size: 40px; }
  .back-02 .line-2 { display: block; font-size: 17px; letter-spacing: 3px; margin-top: 4px; }
  .back-03 .back-block {
    position: absolute; right: 23px; top: 186px; text-align: right;
  }
  .back-03 .company-name { color: var(--white); }
  .back-03 .line-1 { display: block; font-size: 34px; }
  .back-03 .line-2 { display: block; font-size: 16px; letter-spacing: 3px; margin-top: 3px; }
  .back-03 .slogan { margin-top: 4px; font-size: 12px; }
</style>
</head>
<body>
  <section class="card card-front">
    <div class="front-accent"></div>
    <div class="front-info">
      <div class="company-name"><span class="line-1">BROOKVALE</span><span class="line-2">ESTATES LLC</span></div>
      <div class="person-name">DANIEL HARPER</div>
      <div class="person-title">Property Manager</div>
      <div class="address">2750 Alder Creek Road #B210<br>Fresno, CA 93711</div>
      <div class="contact">Phone: 559-404-1187<br>Fax: 559-404-1190<br>daniel@brookvaleestates.us<br>www.brookvaleestates.us</div>
    </div>
  </section>
  <div class="card-label label-front">FRONT CARD</div>

  <section class="card card-back back-01">
    <div class="slogan">Multifamily Property Management</div>
  </section>
  <div class="card-label label-back-01">BACK CARD_01</div>

  <section class="card card-back back-02">
    <div class="company-name"><span class="line-1">BROOKVALE</span><span class="line-2">ESTATES LLC</span></div>
  </section>
  <div class="card-label label-back-02">BACK CARD_02</div>

  <section class="card card-back back-03">
    <div class="back-block">
      <div class="company-name"><span class="line-1">BROOKVALE</span><span class="line-2">ESTATES LLC</span></div>
      <div class="slogan">Multifamily Property Management</div>
    </div>
  </section>
  <div class="card-label label-back-03">BACK CARD_03</div>
</body>
</html>
```